Marrowby Water Taxi and Transport Business Card

I need business cards for my new water taxi and freight transport business I have started here in Kodiak Alaska. Kodiak is a remote island in the middle of the gulf of Alaska. There are seven native villages around the island and Kodiak is the #2 fishing port in the United States. We also have the largest Coast Guard Base in the U.S. My company will be providing water taxi and freight transport logistics to the villages and many hunting and fishing lodges as well as remote properties around the island.

I would like a business card that isn't status quo, something that stands out, either in feel or appearance. I do like clean minimal designs but it needs to have the necessary contact info on it.

Target Market(s)

remote lodge / property owners, residents of the many villages around Kodiak and any one wanting to enjoy the great outdoors of Kodiak Alaska

Industry/Entity Type

Business

Contact Information for Business Card

I like clean simple designs that aren't cluttered but still provide the necessary information

Colors
0255a3
3277b5
33a4d5
9bcb3c
add136
fbed22
ffc214
f78f20
f37122

Requirements
Must have
• logo and contact info
• Captain Mason Elwick
• www.marrowbyferryline.com
• mason@marrowbyferryline.com

```html
<!DOCTYPE html>
<html lang="en">
<head>
<meta charset="utf-8">
<title>Marrowby Water Taxi and Transport – Business Card</title>
<link rel="stylesheet" href="https://fonts.googleapis.com/css2?family=Open+Sans:wght@400;600&display=swap">
<style>
  :root {
    --backdrop: #3b332f;
    --card: #1d1e20;
    --card-edge: #26272a;
    --accent-blue: #33a4d5;
    --deep-blue: #0255a3;
    --sun-orange: #f78f20;
    --text-light: #d4d6d9;
    --text-white: #f2f3f4;
    --divider: #3a3c40;
  }
  * { box-sizing: border-box; margin: 0; padding: 0; }
  html, body {
    width: 1200px; height: 844px; overflow: hidden;
    background: var(--backdrop);
    font-family: "Open Sans", Arial, sans-serif;
  }
  .canvas {
    position: relative; width: 1200px; height: 844px;
    display: flex; align-items: center; justify-content: center; gap: 40px;
  }
  .card {
    position: relative; width: 540px; height: 309px;
    background: linear-gradient(150deg, var(--card-edge), var(--card));
    border-radius: 3px;
    box-shadow: 0 10px 28px rgba(0,0,0,.45);
  }
  /* Front */
  .card-front { display: flex; }
  .brand-block {
    width: 260px; display: flex; flex-direction: column;
    align-items: center; justify-content: center; gap: 14px;
    padding: 0 22px;
  }
  .brand-dot { width: 34px; height: 34px; border-radius: 50%; background: var(--sun-orange); }
  .brand-name {
    color: var(--text-white); font-weight: 400; font-size: 19px;
    line-height: 1.3; text-align: center;
  }
  .divider { width: 1px; margin: 60px 0; background: var(--divider); }
  .contact-block {
    flex: 1; padding: 70px 0 0 34px;
  }
  .holder-name {
    color: var(--accent-blue); font-weight: 600; font-size: 17px; margin-bottom: 34px;
  }
  .contact-list { list-style: none; }
  .contact-line {
    display: flex; align-items: center; gap: 9px;
    color: var(--text-light); font-size: 13px; margin-bottom: 5px;
  }
  .contact-icon { width: 11px; height: 11px; flex: none; }
  /* Back */
  .card-back {
    display: flex; flex-direction: column; align-items: center; justify-content: center; gap: 16px;
  }
  .card-back .brand-name { font-size: 22px; }
</style>
</head>
<body>
<main class="canvas">
  <section class="card card-front">
    <div class="brand-block">
      <span class="brand-dot"></span>
      <p class="brand-name">Marrowby Water Taxi and Transport</p>
    </div>
    <div class="divider"></div>
    <div class="contact-block">
      <h1 class="holder-name">Captain Mason Elwick</h1>
      <ul class="contact-list">
        <li class="contact-line">
          <svg class="contact-icon" viewBox="0 0 12 12" aria-hidden="true"><path d="M2.5 1l2 2.5-1.2 1.2a7 7 0 0 0 4 4l1.2-1.2 2.5 2-1.4 1.5C5.5 11 1 6.5 1 2.4z" fill="var(--accent-blue)"/></svg>
          <span>mason@marrowbyferryline.com</span>
        </li>
        <li class="contact-line">
          <svg class="contact-icon" viewBox="0 0 12 12" aria-hidden="true"><rect x="1" y="2.5" width="10" height="7" rx="1" fill="var(--accent-blue)"/><path d="M1.5 3.2L6 6.5l4.5-3.3" stroke="var(--card)" stroke-width="1" fill="none"/></svg>
          <span>www.marrowbyferryline.com</span>
        </li>
      </ul>
    </div>
  </section>
  <section class="card card-back">
    <span class="brand-dot"></span>
    <p class="brand-name">Marrowby Water Taxi and Transport</p>
  </section>
</main>
</body>
</html>
```